Wine Label Redesign For California Wine Company

We’re looking to refresh our brand with a new professional looking label. We love what we have and was well received over the past three years and would like to keep a couple of the element: Name (Mark Dunlow), it doesn’t have to be in cursive. The swirl, this how everybody recognizes our brand as it’s also in our logo. Colors: Gold and whatever you think is awesome. Looking forward to seeing your work.

Target Market(s)

Retailers

Industry/Entity Type

Winery

Font styles to use
Serif
Script

Colors

Designer to choose colors to be used in the design.

Requirements
Must have
• Front Label:
• Symphony (Varietal)
• 2016 (vintage)
• Lodi, California (location)
• Mark Dunlow (Name)
• Back Label:
• Government Warning
• www.dunlowvinco.com (website)
• 2016 (vintage)
• Swirl
Nice to have
• Creativity
• Bold colors
• Something that pops
Should not have
• Should not look nothing like my old label.

```html
<!DOCTYPE html>
<html lang="en">
<head>
<meta charset="utf-8">
<title>Mark Dunlow Symphony 2016 – Labels</title>
<link rel="stylesheet" href="https://fonts.googleapis.com/css2?family=Cinzel:wght@400;700&family=Arvo:wght@400;700&display=swap">
<style>
  :root {
    --backdrop: #000000;
    --paper: #ffffff;
    --ink: #1c1a17;
    --band: #231f20;
    --gold: #d9b53a;
    --gold-light: #f6efcf;
    --gold-deep: #c9a227;
    --gold-text: #e0bd3f;
  }
  * { box-sizing: border-box; margin: 0; padding: 0; }
  html, body { width: 874px; height: 1200px; overflow: hidden; background: var(--backdrop); }
  .canvas {
    position: relative;
    width: 874px; height: 1200px;
    display: flex; justify-content: center; align-items: center; gap: 38px;
  }
  .label {
    width: 380px; height: 446px;
    display: flex; flex-direction: column;
    background: var(--paper);
  }
  .label-head {
    height: 68px;
    display: flex; align-items: center; justify-content: center;
    color: var(--ink);
  }
  .varietal {
    font-family: "Cinzel", serif;
    font-size: 29px; font-weight: 400;
    letter-spacing: 0.36em; padding-left: 0.36em;
  }
  .website {
    font-family: "Cinzel", serif;
    font-size: 18px; font-weight: 700; letter-spacing: 0.03em;
  }
  .label-field {
    position: relative;
    height: 286px;
    background: linear-gradient(90deg, var(--gold-deep) 0%, var(--gold) 18%, var(--gold-light) 50%, var(--gold) 82%, var(--gold-deep) 100%);
    display: flex; flex-direction: column; align-items: center;
  }
  .brand-mark {
    width: 58px; height: 58px; border-radius: 50%;
    background: var(--ink);
    margin-top: 92px;
  }
  .brand-name {
    font-family: "Cinzel", serif;
    font-weight: 700; font-size: 36px;
    color: var(--ink);
    margin-top: 38px;
    letter-spacing: 0.01em;
  }
  .warning {
    font-family: "Cinzel", serif;
    color: var(--ink);
    text-align: center;
    font-size: 11.5px; line-height: 20.5px;
    padding: 26px 44px 0;
    letter-spacing: 0.02em;
  }
  .warning-title { font-weight: 700; font-size: 13px; display: block; }
  .facts {
    position: absolute; left: 18px; right: 18px; bottom: 30px;
    display: flex; justify-content: space-between;
    font-family: "Cinzel", serif; font-weight: 700; font-size: 11.5px;
    color: var(--ink);
  }
  .label-foot {
    flex: 1;
    background: var(--band);
    display: flex; flex-direction: column; align-items: center;
  }
  .origin {
    font-family: "Arvo", serif;
    font-size: 21px; color: var(--gold-text);
    letter-spacing: 0.16em;
    margin-top: 14px;
  }
  .vintage {
    margin-top: 4px;
    width: 219px; height: 28px;
    background: linear-gradient(90deg, var(--gold-deep), var(--gold-light) 50%, var(--gold-deep));
    font-family: "Arvo", serif; font-weight: 700;
    font-size: 21px; letter-spacing: 0.2em; padding-left: 0.2em;
    color: var(--ink);
    display: flex; align-items: center; justify-content: center;
  }
</style>
</head>
<body>
<main class="canvas">
  <section class="label label-front">
    <header class="label-head"><h1 class="varietal">SYMPHONY</h1></header>
    <div class="label-field" role="img" aria-label="Gold field with a faint repeating ornamental pattern">
      <span class="brand-mark"></span>
      <p class="brand-name">MARK DUNLOW</p>
    </div>
    <footer class="label-foot">
      <p class="origin">Lodi, California</p>
      <p class="vintage">2016</p>
    </footer>
  </section>

  <section class="label label-back">
    <header class="label-head"><p class="website">WWW.DUNLOWVINCO.COM</p></header>
    <div class="label-field" role="img" aria-label="Gold field with a faint repeating ornamental pattern">
      <p class="warning">
        <span class="warning-title">GOVERNMENT WARNING:</span>
        (1) According to the Surgeon General, women should not drink alcoholic beverages during pregnancy because of the risk of birth defects.
        (2) Consumption of alcoholic beverages impairs your ability to drive a car or operate machinery, and may cause health problems.
      </p>
      <div class="facts">
        <span>CONTAINS SULFITES</span>
        <span>ALC 14.2% BY VOL</span>
        <span>750ML</span>
      </div>
    </div>
    <footer class="label-foot">
      <p class="origin">Lodi, California</p>
      <p class="vintage">2016</p>
    </footer>
  </section>
</main>
</body>
</html>
```